Construction company stationary design

We're wanting to develop a new professional stationary set for a newly establised property related business using our existing logo (attached). Business incorporates renovations, property investment and property development.

Specifically needing letter head, business cards, envelopes, email signature and need to get tshirt and caps embroydered.

Looking for something quite modern but professional using white, black and green.

Investment

```html
<!DOCTYPE html>
<html lang="en">
<head>
<meta charset="utf-8">
<title>Kestrel Build — Stationery Set</title>
<link href="https://fonts.googleapis.com/css2?family=Jost:wght@400;500;600&display=swap" rel="stylesheet">
<style>
:root{
  --green:#7dc242;
  --black:#111111;
  --white:#ffffff;
  --paper:#fbfbfb;
  --ink:#444444;
  --rule:#555555;
  --stage:#b87a4b;
  --label:#ffffff;
  --faint:rgba(125,194,66,.12);
  --faint-dark:rgba(255,255,255,.06);
}
*{margin:0;padding:0;box-sizing:border-box}
html,body{width:1200px;height:595px;overflow:hidden}
body{background:var(--stage);font-family:"Jost",Arial,sans-serif;color:var(--ink);position:relative}
.piece{position:absolute;overflow:hidden}
.sheet{background:var(--paper);box-shadow:0 2px 6px rgba(0,0,0,.25)}
.brand{position:absolute;font-family:"Jost",Arial,sans-serif;font-weight:600;color:var(--green);white-space:nowrap;line-height:1;letter-spacing:.5px}
.brand--white{color:var(--white)}
.mark-square{position:absolute;background:var(--faint)}
.mark-square--dark{background:var(--faint-dark)}
.contact-top{position:absolute;right:10px;top:14px;font-size:5.5px;line-height:8px;color:var(--ink);white-space:nowrap}
.dot{display:inline-block;width:4px;height:4px;border-radius:50%;background:var(--green);margin-right:3px;vertical-align:middle}
.footer-line{position:absolute;bottom:6px;font-size:5.5px;color:var(--ink);white-space:nowrap}
.footer-line--tight{font-size:4.6px}
.footer-web{left:0;right:0;text-align:center;letter-spacing:2px}
.caption{position:absolute;color:var(--label);font-size:18px;font-weight:400;text-align:center}
.caption--small{font-size:12px}
.caption--sig{font-size:15px}
.fax-title{position:absolute;left:14px;top:70px;font-size:17px;font-weight:400;color:var(--black)}
.fax-row{position:absolute;font-size:4.5px;border-bottom:.8px solid var(--rule);padding-bottom:1px}
.fax-checks{position:absolute;left:14px;top:162px;display:flex;gap:12px;font-size:4.5px;white-space:nowrap}
.fax-checks span::before{content:"";display:inline-block;width:5px;height:5px;border:.7px solid var(--rule);margin-right:3px;vertical-align:middle}
.envelope{background:var(--white);border:1px solid #999}
.card{box-shadow:0 1px 4px rgba(0,0,0,.3)}
.card--white{background:var(--white)}
.card--green{background:var(--green)}
.card--black{background:var(--black)}
.bc-person{position:absolute;font-size:6px;font-weight:600;color:var(--green);white-space:nowrap}
.bc-contact{position:absolute;font-size:4.8px;line-height:7px;white-space:nowrap}
.card--black .bc-contact{color:#cccccc}
.bc-web{position:absolute;left:0;right:0;text-align:center;font-size:6px;letter-spacing:1.5px}
.garment{background:var(--white)}
.garment__collar{position:absolute;left:0;right:0;top:0;height:6px;background:var(--green)}
.cap{background:var(--black)}
.cap__badge{position:absolute;left:45px;top:45px;width:28px;height:28px;border:2px solid var(--green)}
</style>
</head>
<body>

<!-- Letterhead option 1 -->
<section class="piece sheet" style="left:10px;top:3px;width:254px;height:329px" aria-label="Letterhead option 1">
  <span class="brand" style="left:0;right:0;text-align:center;top:24px;font-size:16px">KESTREL BUILD</span>
  <div class="mark-square" style="left:70px;top:110px;width:90px;height:160px"></div>
  <p class="footer-line footer-line--tight" style="left:14px">12 Harbour Row, Northvale 7315 &nbsp;|&nbsp; 0123 456789 &nbsp;|&nbsp; hello@kestrelbuild.com &nbsp;|&nbsp; www.kestrelbuild.com</p>
</section>
<p class="caption" style="left:10px;top:340px;width:254px">Option-1</p>

<!-- Letterhead option 2 -->
<section class="piece sheet" style="left:290px;top:3px;width:254px;height:329px" aria-label="Letterhead option 2">
  <span class="brand" style="left:11px;top:28px;font-size:14px">KESTREL BUILD</span>
  <div class="contact-top"><div><span class="dot"></span>0123 456789</div><div><span class="dot"></span>hello@kestrelbuild.com</div><div>12 Harbour Row,<br>Northvale 7315</div></div>
  <div class="mark-square" style="left:190px;top:260px;width:60px;height:66px"></div>
  <p class="footer-line footer-web">www.kestrelbuild.com</p>
</section>
<p class="caption" style="left:290px;top:340px;width:254px">Option-2</p>

<!-- Letterhead option 3 / fax -->
<section class="piece sheet" style="left:573px;top:3px;width:254px;height:329px" aria-label="Fax sheet option 3">
  <span class="brand" style="left:13px;top:28px;font-size:14px">KESTREL BUILD</span>
  <div class="contact-top"><div><span class="dot"></span>0123 456789</div><div><span class="dot"></span>hello@kestrelbuild.com</div><div><span class="dot"></span>www.kestrelbuild.com</div></div>
  <h1 class="fax-title">FAX</h1>
  <div class="fax-row" style="left:14px;top:98px;width:120px">To :</div>
  <div class="fax-row" style="left:143px;top:98px;width:88px">From :</div>
  <div class="fax-row" style="left:14px;top:112px;width:120px">Fax :</div>
  <div class="fax-row" style="left:143px;top:112px;width:88px">Pages :</div>
  <div class="fax-row" style="left:14px;top:125px;width:120px">Phone :</div>
  <div class="fax-row" style="left:143px;top:125px;width:88px">Date :</div>
  <div class="fax-row" style="left:14px;top:139px;width:120px">Re :</div>
  <div class="fax-row" style="left:143px;top:139px;width:88px">CC :</div>
  <div class="fax-checks"><span>Urgent</span><span>For Review</span><span>Please Comment</span><span>Please Reply</span><span>Please Recycle</span></div>
  <div class="mark-square" style="left:190px;top:260px;width:60px;height:66px"></div>
  <p class="footer-line" style="left:13px">12 Harbour Row, Northvale 7315</p>
</section>
<p class="caption" style="left:573px;top:340px;width:254px">Option-3</p>

<!-- Envelopes -->
<section class="piece envelope" style="left:908px;top:20px;width:280px;height:126px;border:none" aria-label="Envelope back">
  <svg width="280" height="126" viewBox="0 0 280 126"><path d="M0 0H280V20Q240 55 150 55H130Q40 55 0 20Z" fill="var(--black)"/></svg>
  <span class="brand" style="left:0;right:0;text-align:center;top:28px;font-size:11px">KESTREL BUILD</span>
</section>
<section class="piece envelope" style="left:846px;top:74px;width:284px;height:128px" aria-label="Envelope flap">
  <svg width="284" height="128" viewBox="0 0 284 128" style="position:absolute;left:0;top:0"><path d="M0 0Q150 5 282 0V30Q240 50 150 50H130Q60 50 0 40" fill="none" stroke="#333" stroke-width="1"/></svg>
  <span class="brand" style="left:0;right:0;text-align:center;top:28px;font-size:11px">KESTREL BUILD</span>
</section>
<section class="piece envelope" style="left:876px;top:132px;width:284px;height:127px;border-color:#bbb" aria-label="Envelope front">
  <span class="brand" style="left:8px;top:28px;font-size:13px">KESTREL BUILD</span>
  <p class="footer-line" style="left:8px;top:52px;bottom:auto">12 Harbour Row, Northvale 7315</p>
  <div class="mark-square" style="left:225px;top:75px;width:55px;height:50px"></div>
  <p class="footer-line" style="left:8px;letter-spacing:1.5px">www.kestrelbuild.com</p>
</section>

<!-- Business cards -->
<section class="piece card card--white" style="left:858px;top:277px;width:151px;height:86px" aria-label="Business card white">
  <div class="mark-square" style="left:102px;top:14px;width:44px;height:70px"></div>
  <span class="brand" style="left:6px;top:22px;font-size:11px">KESTREL BUILD</span>
  <p class="bc-person" style="left:6px;top:42px">PERSONS NAME</p>
  <div class="bc-contact" style="left:6px;top:51px"><span class="dot"></span>0123 456789 &nbsp;0123 456789<br><span class="dot"></span>hello@kestrelbuild.com<br>12 Harbour Row, Northvale 7315</div>
</section>
<section class="piece card card--green" style="left:1024px;top:277px;width:151px;height:86px" aria-label="Business card green">
  <span class="brand brand--white" style="left:0;right:0;text-align:center;top:32px;font-size:15px">KESTREL BUILD</span>
  <p class="bc-web" style="top:70px;color:var(--white)">www.kestrelbuild.com</p>
</section>
<section class="piece card card--black" style="left:858px;top:371px;width:151px;height:86px" aria-label="Business card black">
  <div class="mark-square mark-square--dark" style="left:102px;top:14px;width:44px;height:70px"></div>
  <span class="brand" style="left:6px;top:22px;font-size:11px">KESTREL BUILD</span>
  <p class="bc-person" style="left:6px;top:42px">PERSONS NAME</p>
  <div class="bc-contact" style="left:6px;top:51px"><span class="dot"></span>0123 456789 &nbsp;0123 456789<br><span class="dot"></span>hello@kestrelbuild.com<br>12 Harbour Row, Northvale 7315</div>
</section>
<section class="piece card card--black" style="left:1024px;top:371px;width:151px;height:86px" aria-label="Business card black reverse">
  <span class="brand" style="left:0;right:0;text-align:center;top:32px;font-size:15px">KESTREL BUILD</span>
  <p class="bc-web" style="top:70px;color:#cccccc">www.kestrelbuild.com</p>
</section>

<!-- Email signatures -->
<section class="piece card card--white" style="left:818px;top:477px;width:180px;height:79px" aria-label="Email signature 1">
  <div class="mark-square" style="left:125px;top:10px;width:50px;height:66px"></div>
  <span class="brand" style="left:12px;top:24px;font-size:11px">KESTREL BUILD</span>
  <p class="bc-person" style="left:12px;top:40px">PERSONS NAME</p>
  <div class="bc-contact" style="left:12px;top:49px"><span class="dot"></span>0123 456789 &nbsp;0123 456789<br><span class="dot"></span>hello@kestrelbuild.com<br>12 Harbour Row, Northvale 7315</div>
</section>
<section class="piece card card--black" style="left:1006px;top:477px;width:180px;height:79px" aria-label="Email signature 2">
  <div class="mark-square mark-square--dark" style="left:125px;top:10px;width:50px;height:66px"></div>
  <span class="brand" style="left:12px;top:24px;font-size:11px">KESTREL BUILD</span>
  <p class="bc-person" style="left:12px;top:40px">PERSONS NAME</p>
  <div class="bc-contact" style="left:12px;top:49px"><span class="dot"></span>0123 456789 &nbsp;0123 456789<br><span class="dot"></span>hello@kestrelbuild.com<br>12 Harbour Row, Northvale 7315</div>
</section>
<p class="caption caption--sig" style="left:818px;top:562px;width:180px">E.S - 1</p>
<p class="caption caption--sig" style="left:1006px;top:562px;width:180px">E.S - 2</p>

<!-- T-shirt prints -->
<section class="piece garment" style="left:6px;top:379px;width:147px;height:197px" aria-label="T-shirt print option 1">
  <div class="garment__collar"></div>
  <span class="brand" style="left:38px;top:58px;font-size:8px">KESTREL BUILD</span>
  <div class="mark-square" style="left:30px;top:100px;width:80px;height:90px"></div>
</section>
<p class="caption caption--small" style="left:6px;top:579px;width:147px">Option-1</p>
<section class="piece garment" style="left:173px;top:379px;width:147px;height:197px" aria-label="T-shirt print option 2">
  <div class="garment__collar"></div>
  <span class="brand" style="left:40px;top:56px;font-size:10px">KESTREL BUILD</span>
  <div class="mark-square" style="left:30px;top:100px;width:80px;height:90px"></div>
</section>
<p class="caption caption--small" style="left:173px;top:579px;width:147px">Option-2</p>

<!-- Cap embroidery -->
<section class="piece cap" style="left:340px;top:395px;width:185px;height:150px;border-radius:70px 70px 8px 8px" aria-label="Cap front embroidery">
  <span class="brand" style="left:0;right:0;text-align:center;top:62px;font-size:16px">KESTREL BUILD</span>
</section>
<section class="piece cap" style="left:560px;top:405px;width:235px;height:135px;border-radius:70px 70px 8px 8px" aria-label="Cap side embroidery">
  <div class="cap__badge"></div>
</section>

</body>
</html>
```